Cat-products company needs smart, yet endearing, business card

We need a business card design for a new, but up-and-running, business based in Honolulu, Hawaii. The business is Purrnest Nook Co. Our first product is the most environmentally-friendly cat grass kit ever seen on the planet. Future products, currently in the R&D phase, will include a variety of exciting cat scratchers. We also do consulting work to help apartment-dwellers make their home more cat-friendly and, in the future, plan on doing full, custom installs of structure to create high walkways for cats.

Target Market(s)

Middle-aged, apartment-dwelling, middle-class workers who own 1 or more cats and who dote on them.

Industry/Entity Type

Pet Care

Contact Information for Business Card

A striking, professional, yet warm and friendly design is what we're after.

Font styles to use
Serif
Sans Serif
Other font styles liked:
• Comfortaa

Colors

Designer to choose colors to be used in the design.

Requirements
Must have
• The company logo: (see attachment)
• The company name: Purrnest Nook Co
• The web address: www.purrnestnookco.com
• Email: support@purrnestnookco.com
• Phone: +1 (808) 571 6023
• Update (Fri Jun 30 3017 7:45pm Hawaii Time) I would like, is possible, uploaded picture of the cat grass kit on the back of the card with some text along the lines of: Purrnest Nook Co - Maker Of The Leafiest Feline Sprout Set Yet
Nice to have
• A cat picture, cartoon, real or silhouette that illustrates cats in action and/or relaxing; ie using the apartment space to live, play and relax in and being well-contented.
• Most of the website is done in the font: Comfortaa. It might be nice to continue using this for brand consistency.
Should not have
• Hard-to-read fonts.

```html
<!DOCTYPE html>
<html lang="en">
<head>
<meta charset="utf-8">
<title>Purrnest Nook Co – Business Card</title>
<link rel="stylesheet" href="https://fonts.googleapis.com/css2?family=Comfortaa:wght@700&family=PT+Sans:wght@700&family=Questrial&display=swap">
<style>
  :root {
    --backdrop: #2b2b2b;
    --cocoa: #52312b;
    --amber: #f0aa00;
    --paper: #f1f1f1;
    --cream: #f4ece8;
    --ink-grey: #555555;
    --dot: #6b4a42;
  }
  * { margin: 0; padding: 0; box-sizing: border-box; }
  html, body {
    width: 1200px;
    height: 960px;
    overflow: hidden;
    background: var(--backdrop);
  }
  .canvas {
    position: relative;
    width: 1200px;
    height: 960px;
  }
  .card {
    position: absolute;
    width: 600px;
    height: 343px;
    border-radius: 22px;
    overflow: hidden;
  }
  .card-front {
    left: 314px;
    top: 113px;
    background: var(--cocoa);
  }
  .card-back {
    left: 311px;
    top: 472px;
    background: var(--paper);
  }

  /* Front */
  .front-motif {
    position: absolute;
    left: 268px;
    top: 22px;
    width: 310px;
    height: 310px;
  }
  .contact {
    position: absolute;
    left: 39px;
    top: 140px;
    color: var(--cream);
    font-family: "Questrial", sans-serif;
    font-size: 15px;
    line-height: 19px;
  }
  .person-name {
    font-family: "PT Sans", sans-serif;
    font-weight: 700;
    font-size: 22px;
    line-height: 26px;
    color: var(--amber);
    letter-spacing: 0.2px;
  }
  .person-role {
    font-size: 15px;
    margin-bottom: 22px;
  }
  .address { margin-bottom: 10px; }
  .label { color: var(--amber); font-weight: 700; }

  /* Back */
  .social-dots {
    position: absolute;
    right: 16px;
    top: 19px;
    display: flex;
    gap: 2px;
  }
  .social-dot {
    width: 23px;
    height: 23px;
    border-radius: 50%;
    background: var(--dot);
  }
  .brand-mark {
    position: absolute;
    left: 50%;
    top: 70px;
    width: 110px;
    height: 110px;
    margin-left: -55px;
    border-radius: 50%;
    background: var(--cocoa);
  }
  .brand-name {
    position: absolute;
    left: 0;
    right: 0;
    top: 200px;
    text-align: center;
    font-family: "Comfortaa", sans-serif;
    font-weight: 700;
    font-size: 40px;
    color: var(--amber);
  }
  .brand-web {
    position: absolute;
    left: 0;
    right: 0;
    top: 294px;
    text-align: center;
    font-family: "Questrial", sans-serif;
    font-size: 14px;
    letter-spacing: 5px;
    color: var(--ink-grey);
  }
</style>
</head>
<body>
<main class="canvas">
  <section class="card card-front" aria-label="Business card front">
    <svg class="front-motif" viewBox="0 0 310 310" aria-hidden="true">
      <circle cx="155" cy="155" r="150" fill="var(--amber)"/>
    </svg>
    <div class="contact">
      <p class="person-name">LEILANI KAHALE</p>
      <p class="person-role">CEO/FOUNDER</p>
      <p class="address">2419 Hibiscus Row<br>Honolulu, Hawaii 96815</p>
      <p><span class="label">P:</span> +1 (808) 571 6023</p>
      <p>support@purrnestnookco.com</p>
      <p>www.purrnestnookco.com</p>
    </div>
  </section>

  <section class="card card-back" aria-label="Business card back">
    <div class="social-dots" aria-hidden="true">
      <span class="social-dot"></span>
      <span class="social-dot"></span>
      <span class="social-dot"></span>
      <span class="social-dot"></span>
    </div>
    <div class="brand-mark" aria-hidden="true"></div>
    <p class="brand-name">Purrnest Nook Co</p>
    <p class="brand-web">www.purrnestnookco.com</p>
  </section>
</main>
</body>
</html>
```